Illustrations, Icons and placement

Wire frame will describe it best, https://plavido.com/diagrams/kRtmWbNoQeprsLvx

With the direction of my mockups I am going to require illustrations with similarity to the mock up. I need icons for my slider and of course beautiful slides. It is not necessary to design the webpage, I know where I want to go with this, I really just need strong illustrations.

This is the first serious design submitted. I appreciate the obvious hard work. To be honest, this system is not great for designers to know exactly what I want but finding a designer that can put in the effort to get there is the trick.

I have locked in the front page design to something that is very accurately portrayed in the mockup. The reason why is the illustration I will using. Currently My mock up shows flower on a hill, i replace with an brightcrate illustration, see uploaded file to review... Also, colors are definatly what I am looking for but this ok for now. Your design is good..

Reason: my choice needs more time to finish the design before we begin

Target Market(s)

SaaS Consumer

Industry/Entity Type

Work

Requirements
Must have
• Display features in a nice slider like

http://www.drovelink.com/pebblegate/index.php

room in header for new illustration, see attachment
Should not have
• Traditional out dated designs that look like templates

```html
<!DOCTYPE html>
<html lang="en">
<head>
<meta charset="utf-8">
<title>Apps Marketplace</title>
<link rel="stylesheet" href="https://fonts.googleapis.com/css2?family=Tinos:wght@400;700&family=Source+Sans+3:wght@400;600&display=swap">
<style>
:root{
  --page:#0c0b0a;
  --panel:#040404;
  --glow:#3a2412;
  --label:#a98a6a;
  --label-light:#bdbdbd;
  --heading:#cfcfcf;
  --body-brown:#8d7057;
  --accent-gold:#a57b2c;
  --copy-light:#e6e6e6;
  --tab-top:#dcdcdc;
  --tab-bottom:#5a5a5a;
  --list-bg:#f4f4f4;
  --list-text:#333;
  --list-muted:#9a9a9a;
  --scroll:#6b6b6b;
}
*{box-sizing:border-box;margin:0;padding:0}
html,body{width:1200px;height:901px;overflow:hidden}
body{background:radial-gradient(ellipse at 50% 40%,#121110 0%,var(--page) 55%,#050505 100%);position:relative;font-family:"Source Sans 3",sans-serif}

.service-bar{position:absolute;left:108px;top:0;width:957px;height:136px;
  background:linear-gradient(180deg,#140f0b 0%,#0a0807 70%,#0e0b09 100%);
  box-shadow:0 10px 30px -12px var(--glow) inset}
.service{position:absolute;top:0;width:130px;margin-left:-65px;text-align:center}
.service svg{display:block;margin:0 auto;filter:drop-shadow(0 0 8px #6a4020)}
.service-label{position:absolute;left:0;width:100%;font-family:"Tinos",serif;font-weight:700;font-size:15px;line-height:18px;color:var(--label)}
.service-label.light{color:var(--label-light)}

.showcase{position:absolute;left:108px;top:209px;width:391px;height:313px;border-radius:10px 10px 40px 40px;
  background:linear-gradient(135deg,#3a3a3a 0%,#1b1b1b 50%,#0d0d0d 51%,#1a1a1a 100%);border:2px solid #cfcfcf}
.divider{position:absolute;left:541px;top:185px;width:3px;height:358px;
  background:linear-gradient(180deg,transparent,#7a5a3a 50%,transparent)}

.feature{position:absolute;width:225px}
.feature h2{font-family:"Tinos",serif;font-weight:700;font-size:19px;letter-spacing:.5px;color:var(--heading);margin-bottom:9px}
.feature p{font-size:15px;line-height:23px;color:var(--body-brown)}

.category-panel{position:absolute;left:108px;top:568px;width:957px;height:360px;border-radius:14px;
  background:linear-gradient(180deg,var(--panel) 0%,#070605 70%,#1e140c 100%)}
.tab{position:absolute;top:586px;width:60px;height:330px;border-radius:4px 4px 0 0;
  background:linear-gradient(180deg,var(--tab-top),#9a9a9a 55%,var(--tab-bottom))}
.tab span{position:absolute;left:50%;bottom:var(--b);transform:translateX(-50%) rotate(-90deg);transform-origin:center;white-space:nowrap;
  font-size:21px;font-weight:600;color:#f4f4f4;text-shadow:0 1px 3px #222;display:block;width:0;height:0}
.tab span i{font-style:normal;position:absolute;left:0;top:-14px;transform:translateX(0)}

.category-title{position:absolute;left:294px;top:594px;font-family:"Tinos",serif;font-size:24px;color:var(--accent-gold)}
.category-copy{position:absolute;left:299px;top:648px;width:295px;font-size:13.5px;line-height:27.7px;color:var(--copy-light)}

.category-list{position:absolute;left:622px;top:654px;width:163px;height:204px;border-radius:4px;background:var(--list-bg);overflow:hidden}
.category-list ul{list-style:none;position:absolute;left:11px;top:4px}
.category-list li{height:30px;line-height:20px;font-size:14px;color:var(--list-text)}
.category-list li.muted{color:var(--list-muted)}
.category-list li.faint{color:#d2d2d2}
.scrollbar{position:absolute;right:0;top:0;width:13px;height:100%;background:var(--scroll)}
.scroll-thumb{position:absolute;left:2px;top:38px;width:9px;height:43px;background:#fff}
.pointer{position:absolute;left:776px;top:720px}
</style>
</head>
<body>

<header class="service-bar">
  <div class="service" style="left:126px">
    <svg width="112" height="70" viewBox="0 0 112 70"><g fill="#000"><circle cx="30" cy="18" r="13"/><path d="M6 66c0-20 10-32 24-32s24 12 24 32z"/><circle cx="82" cy="18" r="13"/><path d="M58 66c0-20 10-32 24-32s24 12 24 32z"/></g></svg>
    <div class="service-label" style="top:88px">Collaborate</div>
  </div>
  <div class="service" style="left:270px">
    <svg width="80" height="70" viewBox="0 0 80 70"><g fill="#000"><circle cx="30" cy="18" r="13"/><path d="M8 66c0-20 9-32 22-32s22 12 22 32z"/><circle cx="56" cy="28" r="8" fill="none" stroke="#000" stroke-width="3"/><path d="M61 34l11 11" stroke="#000" stroke-width="4"/></g></svg>
    <div class="service-label" style="top:80px">Find<br>Professionals</div>
  </div>
  <div class="service" style="left:406px">
    <svg width="70" height="70" viewBox="0 0 70 70"><g fill="#000"><ellipse cx="30" cy="12" rx="20" ry="6"/><path d="M10 12v40c0 5 9 8 20 8s20-3 20-8V12z"/><path d="M44 50c6 0 12 3 12 8s-6 6-12 4z"/></g></svg>
    <div class="service-label" style="top:80px">Theme<br>Builder</div>
  </div>
  <div class="service" style="left:548px">
    <svg width="90" height="72" viewBox="0 0 90 72"><g fill="#000"><ellipse cx="45" cy="10" rx="38" ry="9"/><path d="M7 14v12c0 5 17 9 38 9s38-4 38-9V14c0 5-17 9-38 9S7 19 7 14z"/><path d="M7 31v12c0 5 17 9 38 9s38-4 38-9V31c0 5-17 9-38 9S7 36 7 31z"/><path d="M7 48v12c0 5 17 9 38 9s38-4 38-9V48c0 5-17 9-38 9S7 53 7 48z"/></g></svg>
    <div class="service-label" style="top:89px">Hosting</div>
  </div>
  <div class="service" style="left:689px">
    <svg width="80" height="72" viewBox="0 0 80 72"><g fill="#000"><path d="M10 60l36-36 6 6-36 36z"/><path d="M40 8l14-4 10 10-4 14-6-6-8 2-2 8-6-6z"/><path d="M66 62l-36-36-6 6 36 36z" transform="translate(-2,-2)"/><path d="M18 6l10 8-4 4-10-8z"/></g></svg>
    <div class="service-label" style="top:80px">Developer<br>Tools</div>
  </div>
  <div class="service" style="left:828px">
    <svg width="70" height="72" viewBox="0 0 70 72"><g fill="#8f8f8f"><circle cx="35" cy="35" r="7"/><path d="M35 0l7 10h-4v14h-6V10h-4zM35 70l7-10h-4V46h-6v14h-4zM0 35l10-7v4h14v6H10v4zM70 35l-10-7v4H46v6h14v4z"/><path d="M12 12l12 2-3 3 8 8-4 4-8-8-3 3zM58 12l-2 12-3-3-8 8-4-4 8-8-3-3zM12 58l2-12 3 3 8-8 4 4-8 8 3 3zM58 58l-12-2 3-3-8-8 4-4 8 8 3-3z"/></g></svg>
    <div class="service-label light" style="top:91px">Distributions</div>
  </div>
</header>

<div class="showcase" role="img" aria-label="Illustration of a desktop monitor showing an app"></div>
<div class="divider"></div>

<section class="feature" style="left:585px;top:207px"><h2>APPS THAT FIT YOU</h2><p>Dictumst purus augue, a amet, lundium augue, cras, etiam dipice parturient augue, tempor cum pellentesque. Lectus</p></section>
<section class="feature" style="left:843px;top:207px;width:215px"><h2>SHARE APPS</h2><p>Sed est sed pulvinar montes arcu nec magna, turpis purus ridiculus. Integer lacus egestas.</p></section>
<section class="feature" style="left:585px;top:383px"><h2>EASY SEARCH</h2><p>Dictumst purus augue, a amet, lundium augue, cras, etiam adipiscing parturient augue, tempor cum pellentesque.</p></section>
<section class="feature" style="left:840px;top:383px"><h2>FAST INSTALL</h2><p>Dictumst purus augue, a amet, lundium augue, cras, etiam adipiscing parturient augue, tempor cum pellentesque.</p></section>

<div class="category-panel"></div>
<div class="tab" style="left:142px"><span style="--b:170px"><i style="transform:translateX(-50%)">Hundreds To Choose From</i></span></div>
<div class="tab" style="left:207px"><span style="--b:220px"><i style="transform:translateX(-50%)">Any Category</i></span></div>
<div class="tab" style="left:846px"><span style="--b:170px"><i style="transform:translateX(-50%)">Fine Tuning</i></span></div>
<div class="tab" style="left:911px"><span style="--b:170px"><i style="transform:translateX(-50%)">Talk To The Authors</i></span></div>
<div class="tab" style="left:975px"><span style="--b:170px"><i style="transform:translateX(-50%)">Sell Your Own</i></span></div>

<h3 class="category-title">Any Category</h3>
<p class="category-copy">Sit egestas scelerisque. Scelerisque hac rhoncus. Porta, quis cras, nascetur odio aenean ac integer, ac. Sed sed tortor purus eros risus integer aliquet dis. Urna sagittis enim, turpis platea sed eu nunc cum tincidunt placerat odio, pulvinar lundium, integer.</p>

<div class="category-list">
  <ul>
    <li class="faint">Social</li>
    <li class="muted">Hotel Booking</li>
    <li>Enterprise</li>
    <li>Project Management</li>
    <li>Ticketing</li>
    <li class="muted">Theme</li>
    <li class="faint">Blog</li>
  </ul>
  <div class="scrollbar"><div class="scroll-thumb"></div></div>
</div>
<svg class="pointer" width="16" height="24" viewBox="0 0 16 24"><path d="M1 1v19l5-5 4 8 3-1-4-8h7z" fill="#fff" stroke="#000" stroke-width="1.2"/></svg>

</body>
</html>
```